NexaBRIDGE new era @ Hyper Digitalization

We need a Brochure that show all our product, services and consulting related to Hyper Digitalization into the industrial internet of things world.
We need a document that can be handled as a electronic brochure, this means that we need to show strong corporate presence, with strong skill of technology, and we have credentials and key sucess projects related to Manufacturing industries.
Key industries that we attend: Automotive, Chemical, Food and Beverage, Mining, Paper and Pulp, Oil and Gas, Energy Management.
We save money to our customer in 6 ways: 1) Eficiency in operation 2) Production Control 3) Hyper Digitalization of Thing Optimizing asset ussage 4) Maintenance and predictive of assets risks 5) Quality Control reducing Cost 6) Augmented Reality in operation and control
Target Market(s)
Manufacturing Industry. CEO of companies that has challenges of saving operation costs into plants of manufacturing.
Industry/Entity Type
Software
Other font styles liked:
- MONTSERRAT
Requirements
Must have
- Technology Enviroment, our logo, our expertise, simple message about what our company does and the DNA, infography of the company, cases of sucess, cases of savings $ using our tecnology and services, what we can do for the customer in a few words
Nice to have
- standarize our colors related to our presentation, futuristic, information related to Artificial Inteligence related to machinery
Should not have
- old version of technology,

```html
<!DOCTYPE html>
<html lang="en">
<head>
<meta charset="utf-8">
<title>NexaBRIDGE Brochure 2021</title>
<link rel="stylesheet" href="https://fonts.googleapis.com/css2?family=Montserrat:wght@400;500;600;700;800&display=swap">
<style>
  :root {
    --canvas: #e6e5e3;
    --navy: #1d4f77;
    --blue: #0c73b5;
    --sky: #35a5dc;
    --ink: #2b2b2b;
    --paper: #f4f4f4;
    --white: #ffffff;
    --rule: #2c6e9e;
  }
  * { margin: 0; padding: 0; box-sizing: border-box; }
  html, body { width: 1109px; height: 1200px; overflow: hidden; }
  body {
    background: var(--canvas);
    font-family: "Montserrat", sans-serif;
    color: var(--ink);
    position: relative;
  }
  .page {
    position: absolute;
    width: 486px; height: 343px;
    overflow: hidden;
    background: linear-gradient(135deg, #ffffff 0%, #ececec 100%);
    box-shadow: 0 4px 10px rgba(0,0,0,.25);
  }
  .page--cover { left: 44px; top: 66px; }
  .page--objective { left: 579px; top: 66px; }
  .page--themes { left: 44px; top: 441px; }
  .page--dna { left: 579px; top: 441px; }
  .page--strategy { left: 318px; top: 814px; }

  .brand {
    font-family: "Montserrat", sans-serif;
    font-weight: 500;
    letter-spacing: .5px;
    white-space: nowrap;
  }
  .section-title {
    position: absolute;
    font-weight: 800;
    font-size: 17px;
    color: var(--sky);
    letter-spacing: .2px;
  }
  .title-rule {
    position: absolute; left: 26px; top: 0;
    width: 1px; height: 47px; background: var(--blue);
  }
  .bullets { position: absolute; list-style: none; }
  .bullets li {
    position: relative;
    padding-left: 16px;
    font-size: 9px;
    line-height: 11.5px;
  }
  .bullets li::before {
    content: "";
    position: absolute; left: 0; top: 2px;
    width: 7px; height: 7px;
    border: 2px solid var(--sky);
    border-radius: 50%;
  }
  .footer-rule {
    position: absolute; left: 0; top: 325px;
    height: 1px; background: var(--rule);
  }
  .page-num {
    position: absolute; top: 318px;
    width: 15px; height: 15px;
    border: 1px solid var(--rule);
    border-radius: 50%;
    background: var(--white);
    font-size: 6px; font-weight: 700;
    display: flex; align-items: center; justify-content: center;
    color: var(--navy);
  }

  /* Cover */
  .cover-photo {
    position: absolute; left: 0; top: 9px; width: 486px; height: 266px;
    background: linear-gradient(180deg, #5e6266 0%, #8a8e92 45%, #6c7074 100%);
  }
  .cover-topline { position: absolute; left: 0; top: 0; width: 486px; height: 9px; background: var(--blue); }
  .cover-header {
    position: absolute; left: 0; top: 9px; width: 486px; height: 56px;
    background: rgba(29,79,119,.88);
    display: flex; align-items: center; justify-content: center;
  }
  .cover-header .brand { color: var(--white); font-size: 26px; }
  .cover-title {
    position: absolute; left: 0; top: 137px; width: 486px; text-align: center;
    color: var(--white); font-weight: 800; font-size: 24px; letter-spacing: -.3px;
  }
  .cover-underline { position: absolute; left: 134px; top: 173px; width: 216px; height: 1px; background: rgba(255,255,255,.8); }
  .cover-underline-bold { position: absolute; left: 207px; top: 172px; width: 72px; height: 3px; background: var(--white); }
  .cover-base {
    position: absolute; left: 0; top: 274px; width: 486px; height: 69px;
    background: linear-gradient(180deg, #ffffff, #ececec);
    border-top: 2px solid var(--blue);
  }
  .service {
    position: absolute; top: 233px; width: 140px; text-align: center;
  }
  .service-badge {
    width: 78px; height: 78px; margin: 0 auto;
    border: 5px solid var(--blue); border-radius: 50%;
    background: var(--white);
    display: flex; align-items: center; justify-content: center;
  }
  .service-art { width: 54px; height: 46px; border-radius: 6px; background: linear-gradient(135deg, #d6e4ee, #9fb7c9); }
  .service-name { color: #111; font-size: 11px; font-weight: 600; letter-spacing: .5px; }
  .service-label { margin-top: 8px; font-size: 8px; font-weight: 700; color: #111; }

  /* Objective */
  .objective-photo {
    position: absolute; left: 0; top: 0; width: 236px; height: 343px;
    background: linear-gradient(180deg, #7a98b4 0%, #5c84a8 40%, #4f7aa0 100%);
  }
  .objective-title-light,
  .objective-title-accent {
    position: absolute; top: 27px; white-space: nowrap;
    font-size: 13.5px; font-weight: 800; letter-spacing: -.1px;
  }
  .objective-title-light { right: 252px; color: var(--white); }
  .objective-title-accent { left: 239px; color: var(--sky); }
  .objective-box {
    position: absolute; left: 225px; top: 53px; width: 261px; height: 55px;
    background: var(--sky); color: var(--white);
    padding: 5px 12px 0 34px;
    font-size: 9px; font-weight: 700; line-height: 11.5px;
  }
  .objective-intro { position: absolute; left: 259px; top: 113px; width: 215px; font-size: 9px; line-height: 11.5px; }
  .objective-list { left: 265px; top: 143px; width: 212px; }
  .objective-list li { margin-bottom: 11px; }
  .objective-brand { position: absolute; left: 36px; top: 290px; color: var(--white); font-size: 24px; }

  /* Themes */
  .themes-photo {
    position: absolute; right: 0; top: 0; width: 290px; height: 343px;
    background: linear-gradient(90deg, rgba(240,240,240,0) 0%, #9b9b9b 45%, #5f5f5f 100%);
  }
  .themes-list { left: 42px; top: 57px; width: 210px; }
  .themes-list li { margin-bottom: 11px; }
  .terms-banner {
    position: absolute; left: 0; top: 174px; width: 225px; height: 22px;
    background: var(--sky); border-radius: 0 11px 11px 0;
    box-shadow: 3px 0 0 var(--blue);
    color: var(--white); font-weight: 800; font-size: 17px;
    padding-left: 37px; line-height: 22px;
  }
  .benefits-list { left: 42px; top: 207px; width: 420px; }
  .benefits-list li { margin-bottom: 7px; }
  .themes-brand { position: absolute; right: 16px; top: 13px; color: var(--white); font-size: 14px; }

  /* DNA */
  .dna-top { position: absolute; left: 0; top: 0; width: 486px; height: 89px; background: linear-gradient(90deg, #f6f6f6, #e9e9e9); }
  .dna-text { position: absolute; left: 42px; top: 52px; width: 420px; font-size: 9px; line-height: 11.5px; }
  .dna-brand { position: absolute; right: 16px; top: 24px; color: var(--blue); font-size: 15px; }
  .dna-photo {
    position: absolute; left: 0; top: 89px; width: 486px; height: 254px;
    background: linear-gradient(135deg, #2f7fb7 0%, #1c6aa6 50%, #145c96 100%);
  }
  .commit-title {
    position: absolute; left: 0; top: 162px; width: 486px; text-align: center;
    color: var(--white); font-weight: 800; font-size: 17px;
  }
  .commit-rule { position: absolute; left: 179px; top: 189px; width: 130px; height: 1px; background: rgba(255,255,255,.8); }
  .commit-rule-bold { position: absolute; left: 222px; top: 188px; width: 35px; height: 3px; background: var(--white); }
  .commit-lines { position: absolute; left: 30px; top: 201px; width: 426px; text-align: center; color: var(--white); font-size: 9px; line-height: 11.5px; }
  .commit-lines p { margin-bottom: 6px; }
  .commit-lines .dot {
    display: inline-block; width: 7px; height: 7px; margin-right: 5px;
    border: 2px solid var(--white); border-radius: 50%; vertical-align: -1px;
  }

  /* Strategy */
  .strategy-text { position: absolute; left: 42px; top: 52px; width: 420px; font-size: 9px; line-height: 11.5px; }
  .strategy-text p { margin-bottom: 6px; }
  .strategy-band { position: absolute; left: 0; top: 145px; width: 486px; height: 137px; background: linear-gradient(90deg, #e4e7ea, #f2f3f4 50%, #e4e7ea); }
  .strategy-diagram { position: absolute; left: 0; top: 145px; }
  .step-label { font-family: "Montserrat", sans-serif; font-size: 7.5px; font-weight: 700; fill: #111; }
  .step-num { font-family: "Montserrat", sans-serif; font-size: 14px; font-weight: 700; fill: var(--white); }
</style>
</head>
<body>

<!-- Cover -->
<section class="page page--cover">
  <div class="cover-photo" role="img" aria-label="Photo of an automated bottling line in a factory"></div>
  <div class="cover-topline"></div>
  <header class="cover-header"><span class="brand">NexaBRIDGE</span></header>
  <h1 class="cover-title">BROCHURE NEXABRIDGE 2021</h1>
  <div class="cover-underline"></div>
  <div class="cover-underline-bold"></div>
  <div class="cover-base"></div>
  <div class="service" style="left:21px">
    <div class="service-badge"><div class="service-art" role="img" aria-label="Icon of an automated factory with a gear"></div></div>
    <p class="service-label">INDUSTRIAL AUTOMATION</p>
  </div>
  <div class="service" style="left:178px">
    <div class="service-badge"><div class="service-art" role="img" aria-label="Icon of a smart factory building with a cloud"></div></div>
    <p class="service-label">INDUSTRY 4.0</p>
  </div>
  <div class="service" style="left:335px">
    <div class="service-badge"><span class="service-name">ORVANTA</span></div>
    <p class="service-label">ORVANTA SOLUTIONS</p>
  </div>
</section>

<!-- Objective -->
<section class="page page--objective">
  <div class="objective-photo" role="img" aria-label="Photo of a solar field with a tower under a blue tint"></div>
  <h2>
    <span class="objective-title-light">OBJECTIVE OF</span>
    <span class="objective-title-accent">BROCHURE / KEY MESSAGES</span>
  </h2>
  <div class="objective-box">Brochure to be delivered by our marketing process and sales, This brochure will be delivered to CEO´s worldwide in Industrial companies.</div>
  <p class="objective-intro">Need to show in a few pages, what we can do for them:</p>
  <ul class="bullets objective-list">
    <li>We offer product and projects to transform operations in manufacturing.</li>
    <li>Our work drives customers to Competitive Advantage Mode.</li>
    <li>We use Artificial Intelligence, Hyper Digitalization and Machine Learning techniques to obtain cost reduction in Production Process, Better Quality Delivery, Asset &amp; Optimization Performance.</li>
    <li>We add productivity without changes into their actual operations in assets</li>
  </ul>
  <span class="brand objective-brand">NexaBRIDGE</span>
  <div class="footer-rule" style="left:236px;width:226px"></div>
  <div class="page-num" style="left:454px">01</div>
</section>

<!-- Themes -->
<section class="page page--themes">
  <div class="themes-photo" role="img" aria-label="Greyscale photo of a worker in a face shield using an angle grinder"></div>
  <div class="title-rule"></div>
  <h2 class="section-title" style="left:36px;top:23px">THEMES</h2>
  <span class="brand themes-brand">NexaBRIDGE</span>
  <ul class="bullets themes-list">
    <li>We offer high performance technology</li>
    <li>State of the art in techniques with Artificial Intelligence and prototypes for new ways of doing manufacturing</li>
    <li>We play the rol as an Architect for a Digital world into the shopfloor operation at Machine Levels</li>
  </ul>
  <div class="terms-banner">TERMS @ BENEFITS</div>
  <ul class="bullets benefits-list">
    <li>Reduce cost operation in manufacturing in 30%</li>
    <li>Save 17% in Energy for production</li>
    <li>Zero Unplanned Downtime in machine level</li>
    <li>Supply Chain optimization by 1% of the cost of goods</li>
    <li>Optimize consistency in recipes by 10% delivers 32% of cost reduction</li>
    <li>Augmented Reality functions, adds 60% of productivity and efficiency at operator levels</li>
  </ul>
  <div class="footer-rule" style="width:454px"></div>
  <div class="page-num" style="left:454px">02</div>
</section>

<!-- DNA -->
<section class="page page--dna">
  <div class="dna-top"></div>
  <div class="title-rule"></div>
  <h2 class="section-title" style="left:36px;top:23px">OUR DNA</h2>
  <span class="brand dna-brand">NexaBRIDGE</span>
  <p class="dna-text">We want all companies to operate in an automated way, to be more efficient and to compete with whoever is globally. We have the knowledge and experience to achieve it.</p>
  <div class="dna-photo" role="img" aria-label="Blue-tinted photo of hands working on industrial machinery"></div>
  <h2 class="commit-title">OUR COMMITMENTS</h2>
  <div class="commit-rule"></div>
  <div class="commit-rule-bold"></div>
  <div class="commit-lines">
    <p><span class="dot"></span>Improve the operation of each company individually.</p>
    <p><span class="dot"></span>Impact the country's competitiveness.</p>
    <p><span class="dot"></span>Support&nbsp; companies to access the highest levels of development, productivity, financing and profitability.</p>
  </div>
  <div class="footer-rule" style="width:454px;background:rgba(255,255,255,.6)"></div>
  <div class="page-num" style="left:454px">03</div>
</section>

<!-- Strategy -->
<section class="page page--strategy">
  <div class="title-rule"></div>
  <h2 class="section-title" style="left:37px;top:23px">CONSULTING STRATEGY</h2>
  <span class="brand dna-brand">NexaBRIDGE</span>
  <div class="strategy-text">
    <p>We know that all customers are in different maturity level of digitalization.</p>
    <p>Our Strategy helps to start simple, low cost and produce big changes</p>
    <p>We have a graphic that represents the levels, and we need to show into a graph that we can help them to take positive path of optimization</p>
  </div>
  <div class="strategy-band"></div>
  <svg class="strategy-diagram" width="486" height="137" viewBox="0 0 486 137" aria-label="Six-step maturity path">
    <g fill="none" stroke-width="2.5" stroke-linecap="round">
      <g stroke="var(--sky)">
        <path d="M46 60 A34 34 0 1 1 80 89"/>
        <path d="M80 89 L80 112 M74 106 L80 112 L86 106"/>
        <path d="M174 60 A34 34 0 1 1 208 89"/>
        <path d="M208 89 L208 112 M202 106 L208 112 L214 106"/>
        <path d="M302 60 A34 34 0 1 1 336 89"/>
        <path d="M336 89 L336 112 M330 106 L336 112 L342 106"/>
      </g>
      <g stroke="var(--blue)">
        <path d="M177 72 A34 34 0 1 1 143 43"/>
        <path d="M143 43 L143 22 M137 28 L143 22 L149 28"/>
        <path d="M306 72 A34 34 0 1 1 272 43"/>
        <path d="M272 43 L272 22 M266 28 L272 22 L278 28"/>
        <path d="M435 72 A34 34 0 1 1 401 43"/>
        <path d="M401 43 L401 22 M395 28 L401 22 L407 28"/>
      </g>
    </g>
    <g>
      <circle cx="80" cy="55" r="24" fill="var(--sky)"/>
      <circle cx="143" cy="72" r="24" fill="var(--blue)"/>
      <circle cx="208" cy="55" r="24" fill="var(--sky)"/>
      <circle cx="272" cy="72" r="24" fill="var(--blue)"/>
      <circle cx="336" cy="55" r="24" fill="var(--sky)"/>
      <circle cx="401" cy="72" r="24" fill="var(--blue)"/>
    </g>
    <g class="step-num" text-anchor="middle">
      <text x="80" y="60">01</text>
      <text x="143" y="77">02</text>
      <text x="208" y="60">03</text>
      <text x="272" y="77">04</text>
      <text x="336" y="60">05</text>
      <text x="401" y="77">06</text>
    </g>
    <g class="step-label" text-anchor="middle">
      <text x="142" y="16">INTERCONNECTED</text>
      <text x="272" y="16">AUTOMATED</text>
      <text x="401" y="16">MANUAL OPERATIONS</text>
      <text x="80" y="124">INDUSTRY 4.0 IIOT</text>
      <text x="208" y="124">STORAGING</text>
      <text x="336" y="124">INSTRUMENTED</text>
    </g>
  </svg>
  <div class="footer-rule" style="width:454px"></div>
  <div class="page-num" style="left:454px">04</div>
</section>

</body>
</html>
```